business card design for a plumbing contractor

i need a double business card for a plumbing business, our initial service is residential Sewer Drain Cleaning.

Target Market(s)

other plumbing Business

Industry/Entity Type

Plumbing

Contact Information for Business Card

www.PipeworksTopMark.example- 5307218394-

Font styles to use
Serif

Colors
ec1f27
0455a3

```html
<!DOCTYPE html>
<html lang="en">
<head>
<meta charset="utf-8">
<title>Pipeworks Top Mark — Business Card</title>
<link rel="stylesheet" href="https://fonts.googleapis.com/css2?family=Open+Sans:wght@400;600;700&display=swap">
<style>
  :root {
    --brand-red: #ec1f27;
    --brand-blue: #0455a3;
    --band-blue: #0d5bc1;
    --taupe: #a89a80;
    --ink: #333333;
    --paper: #ffffff;
    --backdrop: #e4e5e7;
  }
  * { box-sizing: border-box; margin: 0; padding: 0; }
  html, body { width: 1200px; height: 977px; overflow: hidden; }
  body {
    background: var(--backdrop);
    font-family: "Open Sans", Arial, sans-serif;
    display: flex;
    flex-direction: column;
    align-items: center;
    justify-content: center;
    gap: 44px;
  }
  .card {
    position: relative;
    width: 700px;
    height: 400px;
    background: var(--paper);
    box-shadow: 0 6px 18px rgba(0,0,0,0.18);
    overflow: hidden;
  }
  /* Front */
  .card--front { display: flex; flex-direction: column; align-items: center; justify-content: center; gap: 34px; }
  .wordmark {
    display: flex; align-items: center; gap: 10px;
    font-weight: 700; color: var(--taupe); letter-spacing: 0.3px; white-space: nowrap;
  }
  .wordmark__square { width: 20px; height: 20px; background: var(--brand-red); flex: none; }
  .card--front .wordmark { font-size: 46px; }
  .card--front .wordmark__square { width: 30px; height: 30px; }
  .services--front {
    display: flex; gap: 14px; font-size: 13px; letter-spacing: 1.4px;
    color: var(--taupe); text-transform: uppercase;
  }
  /* Back */
  .card--back .wordmark { position: absolute; left: 42px; top: 138px; font-size: 26px; }
  .name-tab { position: absolute; right: 0; top: 40px; width: 22px; height: 62px; background: var(--brand-red); }
  .person { position: absolute; right: 48px; top: 46px; text-align: right; }
  .person__name { font-size: 24px; font-weight: 600; color: var(--brand-blue); line-height: 1.1; }
  .person__role { font-size: 13px; color: var(--ink); }
  .contacts { position: absolute; right: 40px; top: 112px; list-style: none; text-align: right; }
  .contacts li { display: flex; justify-content: flex-end; align-items: center; gap: 10px; font-size: 12px; color: var(--ink); line-height: 22px; white-space: nowrap; }
  .contacts svg { width: 12px; height: 12px; fill: var(--brand-red); flex: none; }
  .wave { position: absolute; left: 0; top: 0; }
  .services--back {
    position: absolute; left: 0; right: 0; bottom: 40px;
    display: flex; justify-content: center; align-items: center; gap: 26px;
    font-size: 15px; font-weight: 700; color: var(--paper); text-transform: uppercase; letter-spacing: 0.6px;
  }
  .services__dot { width: 7px; height: 7px; border-radius: 50%; background: var(--brand-red); }
</style>
</head>
<body>

<section class="card card--front" aria-label="Card front">
  <div class="wordmark"><span>Pipeworks Top Mark</span><span class="wordmark__square"></span></div>
  <p class="services--front">
    <span>Sewer Drain Cleaning</span><span>·</span><span>Maintenance</span><span>·</span><span>Trenchless Pipe Installs</span>
  </p>
</section>

<section class="card card--back" aria-label="Card back">
  <svg class="wave" width="700" height="400" viewBox="0 0 700 400" aria-hidden="true">
    <path d="M0 272 C 150 345, 300 345, 450 300 C 560 265, 640 238, 700 236 L700 400 L0 400 Z" fill="var(--band-blue)"/>
    <path d="M0 261 C 150 334, 300 334, 450 289 C 560 254, 640 227, 700 225" fill="none" stroke="var(--paper)" stroke-width="6"/>
    <path d="M0 251 C 150 324, 300 324, 450 279 C 560 244, 640 217, 700 215" fill="none" stroke="var(--brand-red)" stroke-width="8"/>
  </svg>

  <div class="name-tab"></div>
  <div class="person">
    <p class="person__name">Darren Kowal</p>
    <p class="person__role">Manager</p>
  </div>

  <div class="wordmark"><span>Pipeworks Top Mark</span><span class="wordmark__square"></span></div>

  <ul class="contacts">
    <li>5307218394
      <svg viewBox="0 0 24 24"><path d="M6.6 10.8a15.1 15.1 0 0 0 6.6 6.6l2.2-2.2a1 1 0 0 1 1-.25 11.4 11.4 0 0 0 3.6.57 1 1 0 0 1 1 1V20a1 1 0 0 1-1 1A17 17 0 0 1 3 4a1 1 0 0 1 1-1h3.5a1 1 0 0 1 1 1c0 1.25.2 2.45.57 3.6a1 1 0 0 1-.25 1z"/></svg></li>
    <li>www.PipeworksTopMark.example
      <svg viewBox="0 0 24 24"><circle cx="12" cy="12" r="11"/></svg></li>
    <li>Dispatcher@PipeworksTopMark.example
      <svg viewBox="0 0 24 24"><path d="M2 5h20v14H2z M2 5l10 8 10-8" stroke="var(--paper)" stroke-width="1.5"/></svg></li>
  </ul>

  <p class="services--back">
    <span>Sewer Drain Cleaning</span><span class="services__dot"></span><span>Maintenance</span><span class="services__dot"></span><span>Trenchless Pipe Installs</span>
  </p>
</section>

</body>
</html>
```